Bright Wave Labs

We need a professional letter head format for our company. Now we have a logo but need to desing a new logo also. I have uploaded our old logo. Use the color in the logo and design a new one.

Dear Designers , Need to mention "BWL" and please dont use our old LOGO. we need a new catchy one.

```html
<!DOCTYPE html>
<html lang="en">
<head>
<meta charset="utf-8">
<title>Bright Wave Labs — Letterhead</title>
<link href="https://fonts.googleapis.com/css2?family=Arimo:wght@700&family=Source+Sans+3:wght@400;600&display=swap" rel="stylesheet">
<style>
  :root {
    --navy: #02203a;
    --green: #95c13b;
    --paper: #fcfcfc;
    --backdrop: #e6e6e6;
    --ink: #3a3a3a;
    --ink-dark: #111;
  }
  * { box-sizing: border-box; margin: 0; padding: 0; }
  html, body {
    width: 1200px; height: 1200px; overflow: hidden;
    background: var(--backdrop);
  }
  .letterhead {
    position: absolute; left: 196px; top: 30px;
    width: 808px; height: 1140px;
    background: var(--paper);
    overflow: hidden;
  }
  .letterhead__header { position: absolute; left: 0; top: 0; width: 808px; height: 79px; display: block; }
  .brand {
    position: absolute; left: 0; right: 0; top: 108px;
    display: flex; justify-content: center; align-items: center; gap: 10px;
    font-family: "Source Sans 3", sans-serif; font-weight: 600;
    font-size: 28px; color: var(--navy);
  }
  .brand__dot { width: 20px; height: 20px; border-radius: 50%; background: var(--green); }
  .letter {
    position: absolute; left: 73px; top: 212px; width: 662px;
    font-family: "Source Sans 3", sans-serif; color: var(--ink);
  }
  .letter__greeting {
    font-family: Arimo, sans-serif; font-weight: 700;
    font-size: 17.5px; color: var(--ink-dark); margin-bottom: 20px;
  }
  .letter__para {
    font-size: 15.8px; line-height: 21.1px;
    text-align: justify; margin-bottom: 21.1px;
  }
  .signature {
    position: absolute; left: 73px; top: 809px; width: 126px; height: 66px;
    background: linear-gradient(90deg, #e9e9e9, #f4f4f4);
    border-radius: 4px;
  }
  .footer__rule {
    position: absolute; left: 154px; top: 1077px; width: 501px; height: 1px;
    background: linear-gradient(90deg, transparent, var(--navy) 15%, var(--navy) 85%, transparent);
  }
  .footer__contacts {
    position: absolute; left: 0; right: 0; top: 1080px;
    display: flex; justify-content: center; gap: 8px; align-items: center;
    font-family: "Source Sans 3", sans-serif; font-size: 12.5px; color: var(--ink-dark);
    padding-left: 6px;
  }
  .contact { display: flex; align-items: center; gap: 4px; }
  .contact svg { width: 10px; height: 10px; fill: var(--navy); }
  .footer__address {
    position: absolute; left: 0; right: 0; top: 1102px; text-align: center;
    font-family: "Source Sans 3", sans-serif; font-size: 11px; color: var(--ink-dark);
    padding-left: 6px;
  }
  .letterhead__band { position: absolute; left: 0; bottom: 0; width: 100%; height: 13px; background: var(--green); }
</style>
</head>
<body>
  <main class="letterhead">
    <svg class="letterhead__header" viewBox="0 0 925 90" preserveAspectRatio="none" aria-hidden="true">
      <rect width="925" height="90" fill="var(--navy)"/>
      <path d="M0 90 L0 86 Q462 -54 925 86 L925 90 Z" fill="var(--paper)"/>
      <path d="M38 81 Q462 -25 885 81 Q462 -9 38 81 Z" fill="var(--green)"/>
    </svg>

    <div class="brand"><span class="brand__dot"></span><span class="brand__name">Bright Wave Labs</span></div>

    <section class="letter">
      <p class="letter__greeting">Dear Mr. Carter,</p>
      <p class="letter__para">Lorem Ipsum is simply dummy text of the printing and typesetting industry. Lorem Ipsum has been the industry's standard dummy text ever since the 1500s, when an unknown printer took a galley of type and scrambled it to make a type specimen book. It has survived not only five centuries, but also the leap into electronic typesetting, remaining essentially unchanged.</p>
      <p class="letter__para">The standard chunk of Lorem Ipsum used since the 1500s is reproduced below for those interested. Sections 1.10.32 and 1.10.33 from "de Finibus Bonorum et Malorum" by Cicero are also reproduced in their exact original form, accompanied by English versions from the 1914 translation by H. Rackham</p>
      <p class="letter__para">Lorem Ipsum is simply dummy text of the printing and typesetting industry. Lorem Ipsum has been the industry's standard dummy text ever since the 1500s, when an unknown printer took a galley of type and scrambled it to make a type specimen book. It has survived not only five centuries, but also the leap into electronic typesetting, remaining essentially unchanged. It was popularised in the</p>
      <p class="letter__para">The standard chunk of Lorem Ipsum used since the 1500s is reproduced below for those interested. Sections 1.10.32 and 1.10.33 from "de Finibus Bonorum et Malorum" by Cicero are also reproduced in their exact original form, accompanied by English versions from the 1914 translation by H. Rackham</p>
      <p class="letter__para">The standard chunk of Lorem Ipsum used since the 1500s is reproduced below for those interested. Sections 1.10.32 and 1.10.33 from "de Finibus Bonorum et Malorum" by Cicero are</p>
    </section>

    <div class="signature" role="img" aria-label="Handwritten signature of the sender"></div>

    <footer>
      <div class="footer__rule"></div>
      <div class="footer__contacts">
        <span class="contact">
          <svg viewBox="0 0 10 10" aria-hidden="true"><path d="M2 0.5 L3.6 2.6 L2.8 3.6 Q4 6 6.4 7.2 L7.4 6.4 L9.5 8 L8.3 9.5 Q1.5 8.5 0.5 1.7 Z"/></svg>
          (+945)555-218-407
        </span>
        <span class="contact">
          <svg viewBox="0 0 10 10" aria-hidden="true"><path d="M0.5 2 H9.5 V8.5 H0.5 Z M1.3 2.8 V7.7 H8.7 V2.8 L5 5.6 Z" fill-rule="evenodd"/></svg>
          info@brightwavelabs.com
        </span>
        <span class="contact">
          <svg viewBox="0 0 10 10" aria-hidden="true"><circle cx="5" cy="5" r="4.5"/><path d="M0.5 5 H9.5 M5 0.5 V9.5 M5 0.5 Q2 5 5 9.5 M5 0.5 Q8 5 5 9.5" stroke="#fff" stroke-width="0.7" fill="none"/></svg>
          www.brightwavelabs.com
        </span>
      </div>
      <p class="footer__address">Po. box 201, Street Name, City Name, Zip Code - 00000</p>
    </footer>

    <div class="letterhead__band"></div>
  </main>
</body>
</html>
```